Business card for builder specialising in renovations.

Need a card for our building business. Business name is under Martin Powles.
Have licence number on card ( 527691K)
Contact number (0400 382 415)
Want to work on logo for some business cards and shirts - something with MP or MPB or open to ideas??
No animations, No hammers. Something sharp and eye catching.
Highlight that we are a renovation specialist. Simple on front with extra details on back with some lines to jot down things.

Target Market(s)

Renovators

Industry/Entity Type

Building

Contact Information for Business Card

2 sided with room on back to jot things down.
Extra details on back so front can be simple ..like, renovations, bathrooms, decks, extensions, new builds,

Logo Text

MP

Font styles to use
Serif

Requirements
Must have
• Eye catching design .
• Name : Martin powles
• Licence number
• Contact number - 0400382415
Nice to have
• Some logo design that we can carry through to other forms of advertising
• Local builder
• Quality work
Should not have
• No animations

```html
<!DOCTYPE html>
<html lang="en">
<head>
<meta charset="utf-8">
<title>Martin Powles – Business Card</title>
<link rel="stylesheet" href="https://fonts.googleapis.com/css2?family=Montserrat:wght@500&family=Tinos:wght@400&display=swap">
<style>
  :root {
    --backdrop: #3a3a3c;
    --card: #000000;
    --blue: #29a8e0;
    --white: #ffffff;
    --rule: #d8d8d8;
  }
  * { margin: 0; padding: 0; box-sizing: border-box; }
  html, body { width: 1200px; height: 900px; overflow: hidden; }
  body {
    background: var(--backdrop);
    position: relative;
    font-family: "Tinos", "Times New Roman", serif;
    color: var(--white);
  }
  .card {
    position: absolute;
    left: 250px;
    width: 700px;
    height: 400px;
    background: var(--card);
    border-radius: 26px;
    overflow: hidden;
  }
  .card--front { top: 35px; }
  .card--back { top: 465px; }

  /* Front */
  .brand {
    position: absolute;
    top: 120px;
    left: 0;
    right: 0;
    display: flex;
    justify-content: center;
    align-items: center;
    gap: 18px;
  }
  .brand__square {
    width: 46px;
    height: 46px;
    background: var(--blue);
  }
  .brand__name {
    font-family: "Montserrat", "Helvetica", sans-serif;
    font-weight: 500;
    font-size: 44px;
    letter-spacing: 1px;
    color: var(--white);
  }
  .front__web {
    position: absolute;
    top: 232px;
    left: 0;
    right: 0;
    text-align: center;
    font-size: 22px;
    letter-spacing: 0.5px;
  }
  .accent { color: var(--blue); }
  .services {
    position: absolute;
    top: 288px;
    left: 40px;
    right: 40px;
    height: 36px;
    border: 2px solid var(--blue);
    border-radius: 18px;
    display: flex;
    align-items: center;
    justify-content: center;
    font-size: 16px;
    line-height: 1;
    white-space: nowrap;
    letter-spacing: 0.2px;
  }

  /* Back */
  .holder {
    position: absolute;
    top: 28px;
    right: 52px;
    text-align: right;
  }
  .holder__name {
    font-size: 26px;
    color: var(--blue);
    letter-spacing: 0.5px;
    line-height: 1.1;
  }
  .holder__role { font-size: 15px; }
  .holder__tab {
    position: absolute;
    top: 28px;
    right: 0;
    width: 30px;
    height: 30px;
    background: var(--blue);
  }
  .back__mark {
    position: absolute;
    left: 48px;
    top: 200px;
    display: flex;
    align-items: center;
    gap: 12px;
  }
  .back__mark-square {
    width: 30px;
    height: 30px;
    background: var(--blue);
  }
  .back__mark-name {
    font-family: "Montserrat", "Helvetica", sans-serif;
    font-weight: 500;
    font-size: 26px;
    color: var(--white);
  }
  .note-line {
    position: absolute;
    height: 2px;
    background: var(--rule);
  }
  .note-line--upper { top: 160px; left: 300px; right: 50px; }
  .note-line--lower { top: 355px; left: 210px; right: 200px; }
  .contacts {
    position: absolute;
    top: 180px;
    right: 40px;
    list-style: none;
    text-align: right;
    font-size: 17px;
    line-height: 26px;
    white-space: nowrap;
  }
  .contacts li {
    display: flex;
    justify-content: flex-end;
    align-items: center;
    gap: 8px;
  }
  .contacts .icon { width: 14px; height: 14px; flex: none; }
  .contacts .icon--none { width: 14px; flex: none; }
</style>
</head>
<body>

  <section class="card card--front" aria-label="Card front">
    <div class="brand">
      <span class="brand__square"></span>
      <span class="brand__name">MARTIN POWLES</span>
    </div>
    <p class="front__web">www.<span class="accent">martinpowles</span>.com</p>
    <p class="services">RENOVATIONS, BATHROOMS, DECKS, EXTENSIONS, NEW BUILDS,</p>
  </section>

  <section class="card card--back" aria-label="Card back">
    <span class="holder__tab"></span>
    <div class="holder">
      <p class="holder__name">MARTIN POWLES</p>
      <p class="holder__role">Director</p>
    </div>

    <div class="back__mark">
      <span class="back__mark-square"></span>
      <span class="back__mark-name">MP</span>
    </div>

    <span class="note-line note-line--upper"></span>
    <span class="note-line note-line--lower"></span>

    <ul class="contacts">
      <li><span><span class="accent">Licence:</span> (527691K)</span><span class="icon--none"></span></li>
      <li><span>0400382415</span>
        <svg class="icon" viewBox="0 0 24 24"><path fill="#29a8e0" d="M6.6 10.8a15 15 0 0 0 6.6 6.6l2.2-2.2a1 1 0 0 1 1-.25 11.4 11.4 0 0 0 3.6.57 1 1 0 0 1 1 1V20a1 1 0 0 1-1 1A17 17 0 0 1 3 4a1 1 0 0 1 1-1h3.5a1 1 0 0 1 1 1c0 1.25.2 2.45.57 3.57a1 1 0 0 1-.25 1z"/></svg></li>
      <li><span>info@martinpowles.com</span>
        <svg class="icon" viewBox="0 0 24 24"><rect x="2" y="5" width="20" height="14" rx="1.5" fill="none" stroke="#29a8e0" stroke-width="2"/><path d="M3 6l9 7 9-7" fill="none" stroke="#29a8e0" stroke-width="2"/></svg></li>
      <li><span>www.<span class="accent">martinpowles</span>.com</span>
        <svg class="icon" viewBox="0 0 24 24"><circle cx="12" cy="12" r="9.5" fill="none" stroke="#29a8e0" stroke-width="2"/><ellipse cx="12" cy="12" rx="4" ry="9.5" fill="none" stroke="#29a8e0" stroke-width="1.6"/><path d="M2.5 12h19M4 7h16M4 17h16" stroke="#29a8e0" stroke-width="1.4"/></svg></li>
    </ul>
  </section>

</body>
</html>
```